National Mission Critical Construction Contractor needs Stationery Design to make a bold statement

We are a small commercial construction company, working primarily in mission critical facilities across the U.S.. We have exciting corporate changes going an and a new logo and office space so we need new stationery. The final design should incorporate our new logo and invoke a fresh, high-tech feel while looking simple and modern.

Industry/Entity Type

Construction

Contact Information for Business Card

We are required to list our state licensing qualifications on the back of our card.

Font styles to use
Sans Serif

Requirements
Must have
• We need to have a design for second page of stationery, envelopes both standard and with a window and for a 3 x 4 notepad.

```html
<!DOCTYPE html>
<html lang="en">
<head>
<meta charset="utf-8">
<title>North Arc Construction Management – Stationery</title>
<link rel="stylesheet" href="https://fonts.googleapis.com/css2?family=Questrial&display=swap">
<style>
  :root {
    --brand-blue: #2470b3;
    --brand-ink: #1f67b1;
    --brand-green: #8bbf2a;
    --paper: #f5f5f5;
    --backdrop: #d6d6d6;
    --body-ink: #4a4a4a;
    --rule: #9a9a9a;
  }
  html, body {
    margin: 0;
    padding: 0;
    width: 1200px;
    height: 1000px;
    overflow: hidden;
    background: var(--backdrop);
    font-family: "Questrial", sans-serif;
  }
  .stationery-set { display: block; width: 1200px; height: 1000px; }
  .paper { fill: var(--paper); }
  .band { fill: var(--brand-blue); }
  .swoosh { fill: none; stroke: var(--brand-green); stroke-linecap: round; }
  .spine { stroke: #e2e2e2; stroke-width: 1.2; }
  .brand-dot { fill: #ffffff; stroke: var(--brand-blue); }
  .brand-dot--flap { fill: none; stroke: #ffffff; }
  .brand-name { fill: var(--brand-ink); font-family: "Questrial", sans-serif; text-anchor: middle; letter-spacing: 0.02em; }
  .brand-rule { stroke: #b9c6d4; stroke-width: 0.8; }
  .brand-tagline { fill: var(--brand-ink); font-family: "Questrial", sans-serif; text-anchor: middle; letter-spacing: 0.18em; }
  .detail { fill: var(--body-ink); font-family: "Questrial", sans-serif; }
  .detail-strong { fill: var(--brand-ink); font-weight: 700; }
  .person-name { fill: var(--brand-ink); font-family: "Questrial", sans-serif; font-weight: 700; letter-spacing: 0.04em; }
  .footer-rule { stroke: var(--rule); stroke-width: 0.6; }
  .contact-icon { fill: var(--brand-ink); }
</style>
</head>
<body>
<svg class="stationery-set" width="1200" height="1000" viewBox="0 0 1200 1000" xmlns="http://www.w3.org/2000/svg">

  <!-- Presentation folder -->
  <g class="folder" transform="translate(152 42)">
    <rect class="paper" width="430" height="558" rx="3"/>
    <path class="band" d="M0,0 H430 V386 C300,384 120,396 0,421 Z"/>
    <path class="swoosh" stroke-width="4" d="M0,428 C120,403 300,392 430,393"/>
    <line class="spine" x1="26" y1="0" x2="26" y2="558"/>
    <circle class="brand-dot" cx="214" cy="390" r="33" stroke-width="5"/>
    <text class="brand-name" x="214" y="449" font-size="25">NORTH ARC</text>
    <line class="brand-rule" x1="128" y1="455" x2="300" y2="455"/>
    <text class="brand-tagline" x="214" y="465" font-size="7.6">CONSTRUCTION MANAGEMENT</text>
    <text class="detail" x="214" y="525" font-size="8" text-anchor="middle">www.<tspan class="detail-strong">northarcbuild</tspan>.com</text>
  </g>

  <!-- Letterhead -->
  <g class="letterhead" transform="translate(616 61)">
    <rect class="paper" width="417" height="539"/>
    <path class="band" d="M0,0 H417 V8 C300,10 150,22 0,48 Z"/>
    <path class="swoosh" stroke-width="3" d="M0,53 C150,27 300,14 417,14"/>
    <circle class="brand-dot" cx="81" cy="33" r="22" stroke-width="3.5"/>
    <text class="brand-name" x="81" y="71" font-size="17">NORTH ARC</text>
    <line class="brand-rule" x1="25" y1="75" x2="137" y2="75"/>
    <text class="brand-tagline" x="81" y="81" font-size="4.8">CONSTRUCTION MANAGEMENT</text>
    <line class="footer-rule" x1="25" y1="499" x2="392" y2="499"/>
    <text class="detail" x="25" y="510" font-size="5.6">1280 Harbor Avenue, Suite 210, Portland</text>
    <text class="detail" x="25" y="517" font-size="5.6"><tspan class="detail-strong">T:</tspan> (503) 555-0142 · <tspan class="detail-strong">E:</tspan> info@northarcbuild.com</text>
    <text class="detail" x="392" y="510" font-size="5.6" text-anchor="end">www.<tspan class="detail-strong">northarcbuild</tspan>.com</text>
  </g>

  <!-- Envelope, front -->
  <g class="envelope-front" transform="translate(117 630)">
    <rect class="paper" width="466" height="201"/>
    <path class="band" d="M0,0 H466 V14 C330,15 160,26 0,49 Z"/>
    <path class="swoosh" stroke-width="3" d="M0,54 C160,31 330,20 466,20"/>
    <circle class="brand-dot" cx="81" cy="33" r="22" stroke-width="3.5"/>
    <text class="brand-name" x="81" y="72" font-size="17">NORTH ARC</text>
    <line class="brand-rule" x1="25" y1="76" x2="137" y2="76"/>
    <text class="brand-tagline" x="81" y="82" font-size="4.8">CONSTRUCTION MANAGEMENT</text>
    <text class="detail" x="82" y="175" font-size="5.6" text-anchor="middle">1280 Harbor Avenue</text>
    <text class="detail" x="82" y="182" font-size="5.6" text-anchor="middle">Suite 210, Portland</text>
  </g>

  <!-- Envelope, back -->
  <g class="envelope-back" transform="translate(616 630)">
    <rect class="paper" width="466" height="201"/>
    <path class="band" d="M0,0 H466 L448,65 H20 Z"/>
    <circle class="brand-dot brand-dot--flap" cx="233" cy="34" r="15" stroke-width="2.5"/>
    <text class="detail" x="233" y="178" font-size="5.6" text-anchor="middle">www.northarcbuild.com</text>
  </g>

  <!-- Business card, front -->
  <g class="card-front" transform="translate(410 862)">
    <rect class="paper" width="172" height="97"/>
    <path class="band" d="M0,0 H172 V21 C130,12 70,6 0,6 Z"/>
    <path class="swoosh" stroke-width="1.8" d="M0,9 C70,9 130,14 172,24"/>
    <circle class="brand-dot" cx="128" cy="19" r="11" stroke-width="2"/>
    <text class="brand-name" x="128" y="40" font-size="9">NORTH ARC</text>
    <line class="brand-rule" x1="98" y1="42" x2="158" y2="42"/>
    <text class="brand-tagline" x="128" y="46" font-size="2.7">CONSTRUCTION MANAGEMENT</text>
    <text class="person-name" x="10" y="42" font-size="5">JORDAN REYES</text>
    <text class="detail" x="10" y="47.5" font-size="3.8">General Manager</text>
    <rect class="contact-icon" x="10" y="66.5" width="3.2" height="3.2" rx="0.6"/>
    <rect class="contact-icon" x="10" y="71.5" width="3.2" height="3.2" rx="0.6"/>
    <rect class="contact-icon" x="10" y="76.5" width="3.2" height="3.2" rx="0.6"/>
    <rect class="contact-icon" x="10" y="81.5" width="3.2" height="3.2" rx="0.6"/>
    <text class="detail" x="16" y="69.3" font-size="3.6">(503) 555-0188</text>
    <text class="detail" x="16" y="74.3" font-size="3.6">(503) 555-0142</text>
    <text class="detail" x="16" y="79.3" font-size="3.6">info@northarcbuild.com</text>
    <text class="detail" x="16" y="84.3" font-size="3.6">www.northarcbuild.com</text>
    <text class="detail" x="161" y="79.3" font-size="3.6" text-anchor="end">1280 Harbor Avenue</text>
    <text class="detail" x="161" y="84.3" font-size="3.6" text-anchor="end">Suite 210, Portland</text>
  </g>

  <!-- Business card, back -->
  <g class="card-back" transform="translate(616 862)">
    <rect class="paper" width="173" height="97"/>
    <path class="band" d="M0,0 H173 V18 C120,19 55,33 0,51 Z"/>
    <path class="swoosh" stroke-width="2" d="M0,55 C55,37 120,23 173,22"/>
    <circle class="brand-dot" cx="86" cy="42" r="12" stroke-width="2.2"/>
    <text class="brand-name" x="86" y="66" font-size="9.5">NORTH ARC</text>
    <line class="brand-rule" x1="52" y1="68" x2="120" y2="68"/>
    <text class="brand-tagline" x="86" y="72" font-size="2.9">CONSTRUCTION MANAGEMENT</text>
  </g>

</svg>
</body>
</html>
```